Business Card Design needed for start up company Halvora

In need of a new business card designed for a start up company based in Sydney, Halvora is a new start up innovative Company, our mission it to make property accessible for everyday Australian and to become the leading Real Estate platform in Australia. We want it to be fresh and clean.

Industry/Entity Type

Financial

Contact Information for Business Card

Section for Name
Section for Title

HALVORA - The Strength of Pooling
Mobile:
Direct:

Font styles to use
Sans Serif

Colors
33a6d7
0692cd
0255a3
ffffff

Requirements
Must have
• Logo, all business card details

```html
<!DOCTYPE html>
<html lang="en">
<head>
<meta charset="utf-8">
<title>Halvora Business Card</title>
<link rel="stylesheet" href="https://fonts.googleapis.com/css2?family=Open+Sans:wght@400;600;700;800&display=swap">
<style>
  :root {
    --sky: #4dbdea;
    --sky-deep: #33a6d7;
    --navy: #22409a;
    --ink: #4a4a4a;
    --paper: #ffffff;
    --stage: #2b2b2d;
    --rule: #6d6d6d;
  }
  * { margin: 0; padding: 0; box-sizing: border-box; }
  html, body {
    width: 1200px; height: 1000px; overflow: hidden;
    background: var(--stage);
    font-family: "Open Sans", Arial, sans-serif;
  }
  .canvas { position: relative; width: 1200px; height: 1000px; }
  .card {
    position: absolute; left: 250px; width: 700px; height: 400px;
    overflow: hidden; box-shadow: 0 10px 30px rgba(0,0,0,.45);
  }
  .card--back { top: 60px; background: var(--sky); }
  .card--front { top: 530px; background: var(--paper); }

  .pattern-fill {
    position: absolute; inset: 0;
    background: linear-gradient(135deg, #5cc6ee 0%, #4dbdea 50%, #45b4e3 100%);
  }
  .brand { position: absolute; display: flex; align-items: center; white-space: nowrap; }
  .brand__dot { border-radius: 50%; flex: none; }
  .brand__name { font-weight: 800; color: var(--navy); letter-spacing: -1px; line-height: 1; }

  .card--back .brand { left: 50%; top: 150px; transform: translateX(-50%); gap: 14px; }
  .card--back .brand__dot { width: 92px; height: 92px; background: var(--paper); }
  .card--back .brand__name { font-size: 60px; }
  .tagline {
    position: absolute; left: 0; right: 0; bottom: 34px; text-align: center;
    color: var(--paper); font-size: 13px; letter-spacing: 3.5px; font-weight: 600;
  }

  .card--front .brand { left: 36px; top: 118px; gap: 10px; }
  .card--front .brand__dot { width: 84px; height: 84px; background: var(--sky); }
  .card--front .brand__name { font-size: 44px; }

  .waves { position: absolute; left: 0; bottom: 0; width: 700px; height: 400px; }
  .divider {
    position: absolute; left: 392px; top: 100px; width: 2px; height: 200px; background: var(--rule);
  }
  .details { position: absolute; left: 416px; top: 96px; color: var(--ink); }
  .details__name { font-size: 24px; font-weight: 700; line-height: 1.1; }
  .details__first { color: var(--sky-deep); }
  .details__last { color: var(--navy); }
  .details__title { font-size: 18px; font-weight: 600; color: #666; margin-bottom: 14px; }
  .details__address { font-size: 15px; line-height: 1.2; margin-bottom: 10px; }
  .contact { list-style: none; font-size: 17px; line-height: 1.35; }
  .contact li { display: flex; align-items: center; gap: 12px; }
  .contact svg { width: 14px; height: 14px; flex: none; fill: var(--sky-deep); }
  .accent { color: var(--sky-deep); }
</style>
</head>
<body>
<div class="canvas">

  <section class="card card--back">
    <div class="pattern-fill" role="img" aria-label="Light blue background of swirling ocean wave pattern"></div>
    <div class="brand">
      <span class="brand__dot"></span>
      <span class="brand__name">HALVORA</span>
    </div>
    <p class="tagline">The Strength of Pooling</p>
  </section>

  <section class="card card--front">
    <svg class="waves" viewBox="0 0 700 400" preserveAspectRatio="none" aria-hidden="true">
      <path d="M0 262 C 120 330, 260 360, 420 355 C 540 352, 620 352, 700 380 L700 400 L0 400 Z" fill="var(--sky)"/>
      <path d="M0 248 C 120 320, 260 350, 420 345 C 540 341, 620 340, 700 364 L700 372 C 620 350, 540 350, 420 353 C 260 358, 120 330, 0 258 Z" fill="var(--navy)"/>
    </svg>

    <div class="brand">
      <span class="brand__dot"></span>
      <span class="brand__name">HALVORA</span>
    </div>

    <div class="divider"></div>

    <div class="details">
      <p class="details__name"><span class="details__first">Marcel</span> <span class="details__last">Doyle</span></p>
      <p class="details__title">Director</p>
      <p class="details__address">Your Street Address,<br>Australia, 123</p>
      <ul class="contact">
        <li><svg viewBox="0 0 24 24"><path d="M6.6 10.8a15 15 0 0 0 6.6 6.6l2.2-2.2c.3-.3.7-.4 1-.2 1.1.4 2.3.6 3.6.6.6 0 1 .4 1 1V20c0 .6-.4 1-1 1A17 17 0 0 1 3 4c0-.6.4-1 1-1h3.5c.6 0 1 .4 1 1 0 1.3.2 2.5.6 3.6.1.3 0 .7-.2 1z"/></svg><span>000 123 456 789</span></li>
        <li><svg viewBox="0 0 24 24"><path d="M7 1h10a2 2 0 0 1 2 2v18a2 2 0 0 1-2 2H7a2 2 0 0 1-2-2V3a2 2 0 0 1 2-2zm0 3v14h10V4z"/></svg><span>000 222 3334</span></li>
        <li><svg viewBox="0 0 24 24"><path d="M2 5h20v14H2zm2 2v.5l8 5 8-5V7l-8 5z"/></svg><span>urname@email.com</span></li>
        <li><svg viewBox="0 0 24 24"><path d="M12 2a10 10 0 1 0 0 20 10 10 0 0 0 0-20zm6.9 6h-3a15 15 0 0 0-1.3-3.8A8 8 0 0 1 18.9 8zM12 4c.8 1.2 1.5 2.5 1.9 4h-3.8c.4-1.5 1.1-2.8 1.9-4zM4.3 14a8 8 0 0 1 0-4h3.4a16 16 0 0 0 0 4zm.8 2h3a15 15 0 0 0 1.3 3.8A8 8 0 0 1 5.1 16zm3-8h-3a8 8 0 0 1 4.3-3.8A15 15 0 0 0 8.1 8zM12 20c-.8-1.2-1.5-2.5-1.9-4h3.8c-.4 1.5-1.1 2.8-1.9 4zm2.3-6H9.7a14 14 0 0 1 0-4h4.6a14 14 0 0 1 0 4zm.3 5.8a15 15 0 0 0 1.3-3.8h3a8 8 0 0 1-4.3 3.8zm1.7-5.8a16 16 0 0 0 0-4h3.4a8 8 0 0 1 0 4z"/></svg><span>www.<span class="accent">websitename</span>.com</span></li>
      </ul>
    </div>
  </section>

</div>
</body>
</html>
```